Calendar Design Project: 2025 with Specific Edits

This is a straightforward project where your creativity can shine!
Simply take the existing 2024 calendar and adapt it for 2025 by incorporating the new photos I've attached.
Please keep the overall concept of the 2024 calendar intact—your focus will be on enhancing it with fresh visuals.

I can't wait to see your amazing designs!
I am looking for a talented graphic designer to create a new 2025 calendar with specific adjustments.
Pictures attached.
Requirements:
Calendar Size: 52cm x 34cm
March Folder:
Adjust the image named "attached - DJI-0025" to make the circular road darker to match the rest of the design.
May Folder:
Modify the circled area in the May image to ensure it looks consistent with the other road (reference file: "attached - After").
November Folder:
Clear out the circled area in the November image (reference file: "attached - After1").
Please let me know if you have any questions or need further clarification.
I added to my breif a design i made last year for same client.
2025, calendar should be vertical and not horizontal. and some of the photos attache are "Before" and "After" please include together inside each month of the calendar.
Thank you!
Feel free to adjust any details as necessary!

Hello talented designers!

I’m excited to share that this is my 14th project on the ArtHive platform, and I’ve been fortunate to have successful collaborations in the past. I'm looking forward to creating a new 2025 calendar with your help, and I believe that with your creativity and skills, we can make this project a success as well!

I hope to establish a long-term relationship with a talented team like yours. As an added incentive, I will be offering a bonus for the winner, and I may select more than one winner, so everyone has a chance to shine!

Let’s make something amazing together!

Best
Update:
cancel or before, only place the After picture

Requirements
Must have
• Project Overview Objective: Create a 2025 calendar using the provided images, maintaining the design concept from the 2024 calendar but enhancing it with new visuals. Format: Vertical layout (52cm x 34cm).

```html
<!DOCTYPE html>
<html lang="en">
<head>
<meta charset="utf-8">
<title>Verda Construction Ltd – 2025 Wall Calendar</title>
<link href="https://fonts.googleapis.com/css2?family=Source+Sans+3:wght@400;600;700&display=swap" rel="stylesheet">
<style>
  :root{
    --ink:#1d1d1b;
    --month:#4a4a4a;
    --lime:#8fe000;
    --lime-soft:#e6ffb8;
    --accent:#5fe03a;
    --cell-green:#c9f7b2;
    --cell-grey:#f1f2f1;
    --shadow:rgba(0,0,0,.78);
  }
  *{margin:0;padding:0;box-sizing:border-box}
  html,body{width:1200px;height:848px;overflow:hidden;background:#fff}
  body{position:relative;font-family:"Source Sans 3",sans-serif;color:var(--ink)}

  .page{position:absolute;top:130px;width:385px;height:588px;background:#fff;
        box-shadow:10px 10px 7px var(--shadow);overflow:hidden}
  .page--june{left:9px}
  .page--july{left:411px}
  .page--august{left:808px}

  .page__art{position:absolute;inset:0;width:385px;height:588px}

  .brand{position:absolute;left:34px;top:26px;color:var(--ink);font-weight:700;line-height:1}
  .brand__name{display:flex;align-items:center;gap:4px;font-size:25px;letter-spacing:1px}
  .brand__mark{width:12px;height:12px;background:var(--ink)}
  .brand__sub{font-size:8.4px;letter-spacing:.6px;margin-top:3px;font-weight:700}

  .title{position:absolute;left:18px;top:316px;line-height:1}
  .title__label{display:block;font-size:15.5px;color:var(--accent);letter-spacing:.3px}
  .title__year{display:block;font-size:36px;font-weight:600;margin-top:1px;letter-spacing:.5px}

  .month{position:absolute;right:109px;top:344px;font-size:21px;color:var(--month);letter-spacing:1px;line-height:1}

  .grid{position:absolute;left:18px;top:378px;width:256px;display:grid;
        grid-template-columns:repeat(7,1fr);grid-template-rows:20px repeat(5,25px);
        column-gap:2px;row-gap:6px}
  .grid span{background:var(--cell-grey);font-size:13.5px;display:flex;align-items:flex-end;padding:0 0 1px 4px;line-height:1}
  .grid span:nth-child(7n+1),.grid span:nth-child(7n){background:var(--cell-green)}
  .grid .hd{font-size:4.7px;font-weight:600;align-items:center;justify-content:center;padding:0;letter-spacing:.1px}
  .grid .hd + span:not(.hd){}

  .mini{position:absolute;left:281px;width:86px}
  .mini--first{top:376px}
  .mini--second{top:487px}
  .mini__label{font-size:5.8px;color:var(--month);letter-spacing:.2px;line-height:1;margin-bottom:3px}
  .mini__label b{font-weight:400;color:var(--accent)}
  .mini__grid{display:grid;grid-template-columns:repeat(7,1fr);grid-template-rows:6px repeat(5,8.5px);
              column-gap:1px;row-gap:2px}
  .mini__grid span{background:var(--cell-grey);font-size:4.6px;display:flex;align-items:center;padding-left:2px;line-height:1}
  .mini__grid span:nth-child(7n+1),.mini__grid span:nth-child(7n){background:var(--cell-green)}
  .mini__grid .hd{font-size:2.6px;justify-content:center;padding:0;font-weight:600}

  .footer{position:absolute;left:20px;top:562px;width:350px;display:flex;align-items:center;gap:10px;font-size:4.6px;line-height:1}
  .footer__brand{font-weight:700;font-size:9px;display:flex;align-items:center;gap:2px;color:var(--ink)}
  .footer__brand i{width:5px;height:5px;background:var(--ink);display:block}
  .footer__item b{font-weight:400;color:var(--accent)}
</style>
</head>
<body>

<!-- JUNE -->
<article class="page page--june">
  <svg class="page__art" viewBox="0 0 385 588" aria-hidden="false">
    <defs>
      <linearGradient id="waveTopJun" x1="0" y1="0" x2="1" y2="0"><stop offset="0" stop-color="#ecffc9"/><stop offset=".6" stop-color="#a9ef2a"/><stop offset="1" stop-color="#86dd00"/></linearGradient>
      <linearGradient id="waveLowJun" x1="0" y1="0" x2="0" y2="1"><stop offset="0" stop-color="#8fe000"/><stop offset="1" stop-color="#f4ffe0"/></linearGradient>
      <linearGradient id="photoJun" x1="0" y1="0" x2="0" y2="1"><stop offset="0" stop-color="#b9c1b0"/><stop offset=".35" stop-color="#6f7e5e"/><stop offset=".6" stop-color="#8f9190"/><stop offset="1" stop-color="#a3a5a4"/></linearGradient>
    </defs>
    <path d="M0 0H385V40C250 28 120 60 0 88Z" fill="url(#waveTopJun)"/>
    <path role="img" aria-label="Photo: concrete road slab being paved by a crew under a site canopy" d="M0 84C120 58 240 30 385 40V225C270 236 140 268 0 258Z" fill="url(#photoJun)"/>
    <path d="M0 258C140 268 270 236 385 225V300C280 314 150 300 0 268Z" fill="url(#waveLowJun)"/>
  </svg>
  <div class="brand"><div class="brand__name"><span class="brand__mark"></span>VERDA</div><div class="brand__sub">CONSTRUCTION LTD</div></div>
  <div class="title"><span class="title__label">CALENDAR</span><span class="title__year">2025</span></div>
  <div class="month">JUNE</div>
  <div class="grid">
    <span class="hd">SUNDAY</span><span class="hd">MONDAY</span><span class="hd">TUESDAY</span><span class="hd">WEDNESDAY</span><span class="hd">THURSDAY</span><span class="hd">FRIDAY</span><span class="hd">SATURDAY</span>
    <span>29</span><span>30</span><span></span><span></span><span></span><span></span><span></span>
    <span>1</span><span>2</span><span>3</span><span>4</span><span>5</span><span>6</span><span>7</span>
    <span>8</span><span>9</span><span>10</span><span>11</span><span>12</span><span>13</span><span>14</span>
    <span>15</span><span>16</span><span>17</span><span>18</span><span>19</span><span>20</span><span>21</span>
    <span>22</span><span>23</span><span>24</span><span>25</span><span>26</span><span>27</span><span>28</span>
  </div>
  <div class="mini mini--first"><div class="mini__label">MAY | <b>2025</b></div>
    <div class="mini__grid">
      <span class="hd">SUN</span><span class="hd">MON</span><span class="hd">TUE</span><span class="hd">WED</span><span class="hd">THU</span><span class="hd">FRI</span><span class="hd">SAT</span>
      <span></span><span></span><span></span><span></span><span>1</span><span>2</span><span>3</span>
      <span>4</span><span>5</span><span>6</span><span>7</span><span>8</span><span>9</span><span>10</span>
      <span>11</span><span>12</span><span>13</span><span>14</span><span>15</span><span>16</span><span>17</span>
      <span>18</span><span>19</span><span>20</span><span>21</span><span>22</span><span>23</span><span>24</span>
      <span>25</span><span>26</span><span>27</span><span>28</span><span>29</span><span>30</span><span>31</span>
    </div></div>
  <div class="mini mini--second"><div class="mini__label">JULY | <b>2025</b></div>
    <div class="mini__grid">
      <span class="hd">SUN</span><span class="hd">MON</span><span class="hd">TUE</span><span class="hd">WED</span><span class="hd">THU</span><span class="hd">FRI</span><span class="hd">SAT</span>
      <span></span><span></span><span>1</span><span>2</span><span>3</span><span>4</span><span>5</span>
      <span>6</span><span>7</span><span>8</span><span>9</span><span>10</span><span>11</span><span>12</span>
      <span>13</span><span>14</span><span>15</span><span>16</span><span>17</span><span>18</span><span>19</span>
      <span>20</span><span>21</span><span>22</span><span>23</span><span>24</span><span>25</span><span>26</span>
      <span>27</span><span>28</span><span>29</span><span>30</span><span>31</span><span></span><span></span>
    </div></div>
  <footer class="footer">
    <span class="footer__brand"><i></i>VERDA</span>
    <span class="footer__item"><b>T:</b> +234 800 555 0142</span>
    <span class="footer__item"><b>E:</b> info@verdabuild.com</span>
    <span class="footer__item"><b>W:</b> www.verdabuild.com</span>
    <span class="footer__item"><b>A:</b> Palm Grove Road, Off Harbor Crescent, Central District, Lagos</span>
  </footer>
</article>

<!-- JULY -->
<article class="page page--july">
  <svg class="page__art" viewBox="0 0 385 588">
    <defs>
      <linearGradient id="waveTopJul" x1="0" y1="0" x2="1" y2="0"><stop offset="0" stop-color="#ecffc9"/><stop offset=".6" stop-color="#a9ef2a"/><stop offset="1" stop-color="#86dd00"/></linearGradient>
      <linearGradient id="waveLowJul" x1="0" y1="0" x2="0" y2="1"><stop offset="0" stop-color="#8fe000"/><stop offset="1" stop-color="#f4ffe0"/></linearGradient>
      <linearGradient id="photoJul" x1="0" y1="0" x2="0" y2="1"><stop offset="0" stop-color="#c9d2cf"/><stop offset=".3" stop-color="#5d6e45"/><stop offset=".6" stop-color="#b5704f"/><stop offset="1" stop-color="#c4644a"/></linearGradient>
    </defs>
    <path d="M0 0H385V40C250 28 120 60 0 88Z" fill="url(#waveTopJul)"/>
    <path role="img" aria-label="Photo: piling rig, excavator and crew working on a bridge foundation" d="M0 84C120 58 240 30 385 40V225C270 236 140 268 0 258Z" fill="url(#photoJul)"/>
    <path d="M0 258C140 268 270 236 385 225V300C280 314 150 300 0 268Z" fill="url(#waveLowJul)"/>
  </svg>
  <div class="brand"><div class="brand__name"><span class="brand__mark"></span>VERDA</div><div class="brand__sub">CONSTRUCTION LTD</div></div>
  <div class="title"><span class="title__label">CALENDAR</span><span class="title__year">2025</span></div>
  <div class="month">JULY</div>
  <div class="grid">
    <span class="hd">SUNDAY</span><span class="hd">MONDAY</span><span class="hd">TUESDAY</span><span class="hd">WEDNESDAY</span><span class="hd">THURSDAY</span><span class="hd">FRIDAY</span><span class="hd">SATURDAY</span>
    <span></span><span></span><span>1</span><span>2</span><span>3</span><span>4</span><span>5</span>
    <span>6</span><span>7</span><span>8</span><span>9</span><span>10</span><span>11</span><span>12</span>
    <span>13</span><span>14</span><span>15</span><span>16</span><span>17</span><span>18</span><span>19</span>
    <span>20</span><span>21</span><span>22</span><span>23</span><span>24</span><span>25</span><span>26</span>
    <span>27</span><span>28</span><span>29</span><span>30</span><span>31</span><span></span><span></span>
  </div>
  <div class="mini mini--first"><div class="mini__label">JUNE | <b>2025</b></div>
    <div class="mini__grid">
      <span class="hd">SUN</span><span class="hd">MON</span><span class="hd">TUE</span><span class="hd">WED</span><span class="hd">THU</span><span class="hd">FRI</span><span class="hd">SAT</span>
      <span>29</span><span>30</span><span></span><span></span><span></span><span></span><span></span>
      <span>1</span><span>2</span><span>3</span><span>4</span><span>5</span><span>6</span><span>7</span>
      <span>8</span><span>9</span><span>10</span><span>11</span><span>12</span><span>13</span><span>14</span>
      <span>15</span><span>16</span><span>17</span><span>18</span><span>19</span><span>20</span><span>21</span>
      <span>22</span><span>23</span><span>24</span><span>25</span><span>26</span><span>27</span><span>28</span>
    </div></div>
  <div class="mini mini--second"><div class="mini__label">AUGUST | <b>2025</b></div>
    <div class="mini__grid">
      <span class="hd">SUN</span><span class="hd">MON</span><span class="hd">TUE</span><span class="hd">WED</span><span class="hd">THU</span><span class="hd">FRI</span><span class="hd">SAT</span>
      <span>31</span><span></span><span></span><span></span><span></span><span>1</span><span>2</span>
      <span>3</span><span>4</span><span>5</span><span>6</span><span>7</span><span>8</span><span>9</span>
      <span>10</span><span>11</span><span>12</span><span>13</span><span>14</span><span>15</span><span>16</span>
      <span>17</span><span>18</span><span>19</span><span>20</span><span>21</span><span>22</span><span>23</span>
      <span>24</span><span>25</span><span>26</span><span>27</span><span>28</span><span>29</span><span>30</span>
    </div></div>
  <footer class="footer">
    <span class="footer__brand"><i></i>VERDA</span>
    <span class="footer__item"><b>T:</b> +234 800 555 0142</span>
    <span class="footer__item"><b>E:</b> info@verdabuild.com</span>
    <span class="footer__item"><b>W:</b> www.verdabuild.com</span>
    <span class="footer__item"><b>A:</b> Palm Grove Road, Off Harbor Crescent, Central District, Lagos</span>
  </footer>
</article>

<!-- AUGUST -->
<article class="page page--august">
  <svg class="page__art" viewBox="0 0 385 588">
    <defs>
      <linearGradient id="waveTopAug" x1="0" y1="0" x2="1" y2="0"><stop offset="0" stop-color="#ecffc9"/><stop offset=".6" stop-color="#a9ef2a"/><stop offset="1" stop-color="#86dd00"/></linearGradient>
      <linearGradient id="waveLowAug" x1="0" y1="0" x2="0" y2="1"><stop offset="0" stop-color="#8fe000"/><stop offset="1" stop-color="#f4ffe0"/></linearGradient>
      <linearGradient id="photoAug" x1="0" y1="0" x2="0" y2="1"><stop offset="0" stop-color="#d7dcd8"/><stop offset=".35" stop-color="#6f8a5c"/><stop offset=".65" stop-color="#5c605e"/><stop offset="1" stop-color="#8e8c86"/></linearGradient>
    </defs>
    <path d="M0 0H385V40C250 28 120 60 0 88Z" fill="url(#waveTopAug)"/>
    <path role="img" aria-label="Photo: dump truck feeding an asphalt paver while a crew resurfaces a road" d="M0 84C120 58 240 30 385 40V225C270 236 140 268 0 258Z" fill="url(#photoAug)"/>
    <path d="M0 258C140 268 270 236 385 225V300C280 314 150 300 0 268Z" fill="url(#waveLowAug)"/>
  </svg>
  <div class="brand"><div class="brand__name"><span class="brand__mark"></span>VERDA</div><div class="brand__sub">CONSTRUCTION LTD</div></div>
  <div class="title"><span class="title__label">CALENDAR</span><span class="title__year">2025</span></div>
  <div class="month">AUGUST</div>
  <div class="grid">
    <span class="hd">SUNDAY</span><span class="hd">MONDAY</span><span class="hd">TUESDAY</span><span class="hd">WEDNESDAY</span><span class="hd">THURSDAY</span><span class="hd">FRIDAY</span><span class="hd">SATURDAY</span>
    <span>31</span><span></span><span></span><span></span><span></span><span>1</span><span>2</span>
    <span>3</span><span>4</span><span>5</span><span>6</span><span>7</span><span>8</span><span>9</span>
    <span>10</span><span>11</span><span>12</span><span>13</span><span>14</span><span>15</span><span>16</span>
    <span>17</span><span>18</span><span>19</span><span>20</span><span>21</span><span>22</span><span>23</span>
    <span>24</span><span>25</span><span>26</span><span>27</span><span>28</span><span>29</span><span>30</span>
  </div>
  <div class="mini mini--first"><div class="mini__label">JULY | <b>2025</b></div>
    <div class="mini__grid">
      <span class="hd">SUN</span><span class="hd">MON</span><span class="hd">TUE</span><span class="hd">WED</span><span class="hd">THU</span><span class="hd">FRI</span><span class="hd">SAT</span>
      <span></span><span></span><span>1</span><span>2</span><span>3</span><span>4</span><span>5</span>
      <span>6</span><span>7</span><span>8</span><span>9</span><span>10</span><span>11</span><span>12</span>
      <span>13</span><span>14</span><span>15</span><span>16</span><span>17</span><span>18</span><span>19</span>
      <span>20</span><span>21</span><span>22</span><span>23</span><span>24</span><span>25</span><span>26</span>
      <span>27</span><span>28</span><span>29</span><span>30</span><span>31</span><span></span><span></span>
    </div></div>
  <div class="mini mini--second"><div class="mini__label">SEPTEMBER | <b>2025</b></div>
    <div class="mini__grid">
      <span class="hd">SUN</span><span class="hd">MON</span><span class="hd">TUE</span><span class="hd">WED</span><span class="hd">THU</span><span class="hd">FRI</span><span class="hd">SAT</span>
      <span></span><span>1</span><span>2</span><span>3</span><span>4</span><span>5</span><span>6</span>
      <span>7</span><span>8</span><span>9</span><span>10</span><span>11</span><span>12</span><span>13</span>
      <span>14</span><span>15</span><span>16</span><span>17</span><span>18</span><span>19</span><span>20</span>
      <span>21</span><span>22</span><span>23</span><span>24</span><span>25</span><span>26</span><span>27</span>
      <span>28</span><span>29</span><span>30</span><span></span><span></span><span></span><span></span>
    </div></div>
  <footer class="footer">
    <span class="footer__brand"><i></i>VERDA</span>
    <span class="footer__item"><b>T:</b> +234 800 555 0142</span>
    <span class="footer__item"><b>E:</b> info@verdabuild.com</span>
    <span class="footer__item"><b>W:</b> www.verdabuild.com</span>
    <span class="footer__item"><b>A:</b> Palm Grove Road, Off Harbor Crescent, Central District, Lagos</span>
  </footer>
</article>

</body>
</html>
```